The quiet harbor with an elephant incorporated in the background

Target Market(s)

Real estate

Industry/Entity Type

Real Estate

Contact Information for Business Card

On back on want my name & number
In front I want the business name, "the quiet harbor", below to say staging & design

Logo Text

The quiet harbor

Font styles to use
Serif

Colors
000000

Requirements
Must have
• I want an elephant behind the writing in gold transperant

```html
<!DOCTYPE html>
<html lang="en">
<head>
<meta charset="utf-8">
<title>The Quiet Harbor – Business Cards</title>
<link rel="stylesheet" href="https://fonts.googleapis.com/css2?family=Cinzel:wght@400&family=Open+Sans:wght@400;700&family=Quicksand:wght@300&display=swap">
<style>
  :root {
    --page-bg: #e9e7e3;
    --card-dark: #262526;
    --card-dark-back: #221f20;
    --gold: #ffb400;
    --gold-soft: rgba(255, 180, 0, 0.16);
    --gold-fade: rgba(255, 180, 0, 0);
    --white: #ffffff;
    --muted: #8a8a8a;
    --card-w: 620px;
    --card-h: 354px;
  }
  * { box-sizing: border-box; margin: 0; padding: 0; }
  html, body {
    width: 1200px;
    height: 900px;
    overflow: hidden;
    background: var(--page-bg);
  }
  .sheet {
    width: 1200px;
    height: 900px;
    display: flex;
    flex-direction: column;
    align-items: center;
    justify-content: center;
    gap: 56px;
  }
  .card {
    position: relative;
    width: var(--card-w);
    height: var(--card-h);
    overflow: hidden;
    box-shadow: 0 6px 18px rgba(0,0,0,0.18);
  }

  /* Soft gold area reserved for the transparent elephant artwork */
  .elephant-art {
    position: absolute;
    border-radius: 50%;
    background: radial-gradient(ellipse at center, var(--gold-soft) 0%, var(--gold-fade) 70%);
  }

  /* Brand lockup */
  .brand {
    position: relative;
    display: flex;
    flex-direction: column;
    align-items: flex-start;
  }
  .brand__mark {
    width: 44px;
    height: 44px;
    margin: 0 0 10px 168px;
    background: var(--white);
  }
  .brand__name {
    font-family: "Cinzel", serif;
    font-weight: 400;
    font-size: 32px;
    letter-spacing: 0.5px;
    line-height: 1;
    color: var(--white);
    white-space: nowrap;
  }
  .brand__tagline {
    font-family: "Quicksand", sans-serif;
    font-weight: 300;
    font-size: 17px;
    letter-spacing: 1px;
    color: var(--muted);
    margin: 2px 0 0 96px;
  }

  /* Front: brand card */
  .card--front {
    background: var(--card-dark);
    display: flex;
    align-items: center;
    justify-content: center;
  }
  .card--front .elephant-art {
    left: 170px; top: 52px; width: 280px; height: 250px;
  }

  /* Back: contact card */
  .card--back { background: var(--card-dark-back); }
  .card__shapes { position: absolute; inset: 0; }
  .contact-name {
    position: absolute;
    left: 60px;
    top: 14px;
    font-family: "Open Sans", sans-serif;
    font-weight: 700;
    font-size: 19px;
    color: var(--gold);
  }
  .contact-details {
    position: absolute;
    left: 22px;
    top: 128px;
    font-family: "Open Sans", sans-serif;
    font-size: 14.5px;
    line-height: 1.38;
    color: var(--white);
    list-style: none;
  }
  .contact-details li { display: flex; align-items: center; gap: 6px; }
  .contact-details .icon { width: 12px; height: 12px; flex: none; }
  .card--back .elephant-art {
    left: 330px; top: 104px; width: 250px; height: 200px;
  }
  .brand--back {
    position: absolute;
    left: 318px;
    top: 122px;
  }
  .brand--back .brand__mark {
    width: 38px; height: 38px; margin: 0 0 10px 150px;
    background: var(--gold);
  }
  .brand--back .brand__name { color: var(--gold); font-size: 27px; }
  .brand--back .brand__tagline { font-size: 15px; margin-left: 86px; }
</style>
</head>
<body>
<main class="sheet">

  <section class="card card--front" aria-label="Business card front">
    <div class="elephant-art" role="img" aria-label="Transparent gold elephant behind the business name"></div>
    <div class="brand">
      <span class="brand__mark" aria-hidden="true"></span>
      <p class="brand__name">The Quiet Harbor</p>
      <p class="brand__tagline">staging &amp; design</p>
    </div>
  </section>

  <section class="card card--back" aria-label="Business card back">
    <svg class="card__shapes" viewBox="0 0 620 354" width="620" height="354" aria-hidden="true">
      <rect x="8" y="8" width="38" height="34" fill="var(--gold)"/>
      <line x1="30" y1="10" x2="16" y2="40" stroke="var(--card-dark-back)" stroke-width="3"/>
      <polygon points="0,262 262,262 250,282 0,282" fill="var(--gold)"/>
      <polygon points="282,276 620,276 620,354 234,354" fill="var(--gold)"/>
    </svg>

    <p class="contact-name">Daniel Marsh</p>

    <ul class="contact-details">
      <li>48 Harbor Lane, Stillwater</li>
      <li>Bayside County, 204518</li>
      <li>
        <svg class="icon" viewBox="0 0 12 12" aria-hidden="true"><path d="M2.5 1 L4.5 1 L5.2 3.6 L4 4.6 Q5.2 7 7.4 8 L8.4 6.8 L11 7.5 L11 9.5 Q10.5 11 9 11 Q2 10 1 3 Q1 1.5 2.5 1 Z" fill="var(--gold)"/></svg>
        (055)-318-2046
      </li>
      <li>
        <svg class="icon" viewBox="0 0 12 12" aria-hidden="true"><rect x="0.5" y="2.5" width="11" height="7.5" fill="var(--gold)"/><path d="M0.5 2.8 L6 7 L11.5 2.8" fill="none" stroke="var(--card-dark-back)" stroke-width="1"/></svg>
        hello@quietharbor.com
      </li>
    </ul>

    <div class="elephant-art" role="img" aria-label="Transparent gold elephant behind the business name"></div>
    <div class="brand brand--back">
      <span class="brand__mark" aria-hidden="true"></span>
      <p class="brand__name">The Quiet Harbor</p>
      <p class="brand__tagline">staging &amp; design</p>
    </div>
  </section>

</main>
</body>
</html>
```